RB Halden Electric Yard Sign

Looking to have a yard sign designed that we can place at projects we are working on. Most likely will be 18" H x 24" W but flexible that we can increase the size if necessary. It should include our logo, our phone # 609-555-0147, website rbhaldenelectric.example and slogan, built on integrity, driven by excellence. Colors should match our brand.

```html
<!DOCTYPE html>
<html lang="en">
<head>
<meta charset="utf-8">
<title>RB Halden Electric Yard Sign</title>
<link href="https://fonts.googleapis.com/css2?family=Montserrat:wght@600;700;800&display=swap" rel="stylesheet">
<style>
  :root {
    --navy: #0b3268;
    --red: #e21f2a;
    --white: #ffffff;
    --backdrop: #e9ece6;
  }
  * { margin: 0; padding: 0; box-sizing: border-box; }
  html, body { width: 1200px; height: 1200px; overflow: hidden; }
  body {
    background: var(--backdrop);
    font-family: "Montserrat", Arial, sans-serif;
    position: relative;
  }
  .yard-sign {
    position: absolute;
    left: 40px; top: 180px;
    width: 1120px; height: 840px;
    overflow: hidden;
    background: var(--white);
    box-shadow: 0 6px 18px rgba(0,0,0,.18);
  }
  .sign-artwork { position: absolute; inset: 0; width: 100%; height: 100%; }
  .brand {
    position: absolute; top: 105px; left: 0; right: 0;
    display: flex; justify-content: center; align-items: center; gap: 14px;
  }
  .brand-dot {
    width: 30px; height: 30px; border-radius: 50%;
    background: var(--navy);
  }
  .brand-name {
    font-weight: 800; font-size: 50px; color: var(--red);
    letter-spacing: .5px; line-height: 1;
  }
  .slogan {
    position: absolute; top: 462px; left: 0; right: 0;
    text-align: center; color: var(--white);
    font-weight: 800; font-size: 72px; line-height: 78px;
    letter-spacing: .5px; text-transform: uppercase;
  }
  .phone-band {
    position: absolute; top: 618px; left: 46px; right: 46px; height: 130px;
    background: linear-gradient(90deg, var(--navy) 0%, #7a2444 18%, var(--red) 38%, var(--red) 62%, #7a2444 82%, var(--navy) 100%);
    display: flex; align-items: center; justify-content: center;
  }
  .phone-number {
    color: var(--white); font-weight: 800; font-size: 116px;
    letter-spacing: 1px; line-height: 1;
  }
  .website {
    position: absolute; top: 752px; left: 84px; right: 84px; height: 50px;
    display: flex; align-items: center; gap: 18px;
  }
  .website-rule { flex: 1; height: 2px; background: var(--white); }
  .website-url {
    color: var(--white); font-weight: 700; font-size: 38px; line-height: 1;
  }
</style>
</head>
<body>
  <div class="yard-sign">
    <svg class="sign-artwork" viewBox="0 0 1292 968" preserveAspectRatio="none" aria-hidden="true">
      <rect width="1292" height="968" fill="var(--white)"/>
      <polygon class="accent-band" points="0,170 646,495 1292,170 1292,198 646,523 0,198" fill="var(--red)"/>
      <polygon class="navy-field" points="0,214 646,539 1292,214 1292,968 0,968" fill="var(--navy)"/>
    </svg>

    <div class="brand">
      <span class="brand-dot"></span>
      <span class="brand-name">RB Halden Electric</span>
    </div>

    <p class="slogan">Built on integrity,<br>driven by excellence</p>

    <div class="phone-band">
      <span class="phone-number">609-555-0147</span>
    </div>

    <div class="website">
      <span class="website-rule"></span>
      <span class="website-url">rbhaldenelectric.example</span>
      <span class="website-rule"></span>
    </div>
  </div>
</body>
</html>
```